Cobalt Meadow Services Business Card Design

I require a business card design for my business Cobalt Meadow Services. The purpose of this business is to enable people to make positive change in their lives. This business offers life coaching, hypnotherapy and facilitation services. The slogan is 'Grow with purpose and live the life you choose.' Coaching services will be available internationally whilst the hypnotherapy and facilitation services will focus on delivery in south east Queensland.

The business card should be crisp, clean, professional and give the client positive feelings of achieving success.

The logo must be representative of a phoenix rising from the ashes which is a symbol of regeneration and new life. My preference is a black Phoenix on a white background similar to the Phoenix image attached to this brief. I'm happy to see other concepts you have too. The logo and business name must be scalable so it can be printed on a large outdoor sign. Therefore the following files must be provided as a minimum:
-Business card
-Logo on it's own
-Business name on it's own

The following detail must appear on either the front/back of the business card
-Logo
-Cobalt Meadow Services
-Grow with purpose and live the life you choose.
-Personal and business success through
-Coaching | Hypnotherapy | Facilitation
-Janet Holloway
-Founder

-Life Coach
-Clinical Hypnotherapist
-MBA (Project Management specialisation)
-Neuro Linguistic Programming Practitioner

-0412 385 976
-E: cobaltmeadow.au@postvale.net
-www.cobalt-meadow.com.au
-Contact us now for your free 20min assessment

Please feel free to ask me as many questions as you like :) Thank you.

Hi all,  friendly reminder that the logo needs to be your own design and cannot be a Imagecrate or other purchased or free image.  

Thanks heaps
Keep the great designs coming in. You're all so talented.
Janet

• Feedback from older people is that black backgrounds with lighter fonts are difficult to read so please no black backgrounds.

```html
<!DOCTYPE html>
<html lang="en">
<head>
<meta charset="utf-8">
<title>Cobalt Meadow Services – Business Card</title>
<link href="https://fonts.googleapis.com/css2?family=Open+Sans:ital,wght@0,400;0,600;1,400&display=swap" rel="stylesheet">
<style>
  :root {
    --bg: #e9e9e9;
    --card: #ffffff;
    --ink: #3a3a3a;
    --ink-soft: #6a6a6a;
    --rule: #b5b5b5;
    --orange: #f28a12;
    --orange-deep: #ef7f0a;
    --yellow: #f7d70f;
  }
  * { box-sizing: border-box; margin: 0; padding: 0; }
  html, body { width: 1200px; height: 1200px; overflow: hidden; }
  body {
    background: var(--bg);
    font-family: "Open Sans", Arial, sans-serif;
    color: var(--ink);
    display: flex;
    flex-direction: column;
    align-items: center;
    justify-content: center;
    gap: 70px;
  }
  .card {
    position: relative;
    width: 800px;
    height: 480px;
    background: var(--card);
    box-shadow: 0 6px 22px rgba(0,0,0,0.12);
    overflow: hidden;
  }

  /* Front */
  .card--front .brand {
    position: absolute;
    left: 150px;
    top: 110px;
  }
  .slogan {
    font-size: 19px;
    font-style: italic;
    color: var(--ink-soft);
    margin-bottom: 16px;
    margin-left: 4px;
  }
  .brand-row {
    display: flex;
    align-items: center;
    gap: 18px;
  }
  .brand-dot {
    width: 74px;
    height: 74px;
    border-radius: 50%;
    background: var(--orange);
    flex: none;
  }
  .brand-name {
    font-weight: 600;
    color: var(--orange);
    font-size: 40px;
    line-height: 1.05;
  }
  .front-rule {
    width: 470px;
    height: 1px;
    background: var(--rule);
    margin: 22px 0 16px;
  }
  .front-list { list-style: none; }
  .front-list li {
    display: flex;
    align-items: center;
    gap: 10px;
    font-size: 19px;
    line-height: 1.45;
    color: var(--ink);
  }
  .front-list li::before {
    content: "";
    width: 10px;
    height: 8px;
    background: var(--ink);
    border-radius: 1px;
    flex: none;
  }

  /* Back */
  .card--back .brand-small {
    position: absolute;
    left: 60px;
    top: 70px;
    display: flex;
    align-items: center;
    gap: 12px;
  }
  .brand-small .brand-dot { width: 44px; height: 44px; }
  .brand-small .brand-name { font-size: 24px; }
  .credentials {
    position: absolute;
    left: 330px;
    top: 150px;
    list-style: none;
    font-size: 18px;
    line-height: 1.4;
  }
  .credentials li::before { content: "• "; }
  .contacts {
    position: absolute;
    left: 330px;
    top: 275px;
    list-style: none;
    font-size: 21px;
    line-height: 1.5;
  }
  .contacts li { display: flex; align-items: center; gap: 10px; }
  .contact-icon { width: 20px; height: 20px; flex: none; }
  .offer-band {
    position: absolute;
    left: 0;
    right: 0;
    bottom: 0;
    height: 58px;
    background: linear-gradient(90deg, var(--orange-deep) 0%, var(--yellow) 40%, var(--yellow) 60%, var(--orange-deep) 100%);
    display: flex;
    align-items: center;
    justify-content: center;
    font-size: 20px;
    color: var(--ink);
  }
</style>
</head>
<body>

  <section class="card card--front">
    <div class="brand">
      <p class="slogan">‘Grow with purpose and live the life you choose.’</p>
      <div class="brand-row">
        <span class="brand-dot"></span>
        <span class="brand-name">Cobalt Meadow<br>Services</span>
      </div>
      <div class="front-rule"></div>
      <ul class="front-list">
        <li>Personal and business success through</li>
        <li>Coaching | Hypnotherapy | Facilitation</li>
        <li>Janet Holloway</li>
        <li>Founder</li>
      </ul>
    </div>
  </section>

  <section class="card card--back">
    <div class="brand-small">
      <span class="brand-dot"></span>
      <span class="brand-name">Cobalt Meadow Services</span>
    </div>
    <ul class="credentials">
      <li>Life Coach</li>
      <li>Clinical Hypnotherapist</li>
      <li>MBA (Project Management specialisation)</li>
      <li>Neuro Linguistic Programming Practitioner</li>
    </ul>
    <ul class="contacts">
      <li>
        <svg class="contact-icon" viewBox="0 0 20 20" aria-hidden="true"><circle cx="10" cy="10" r="10" fill="#f28a12"/><path d="M7 5h2l1 3-1.5 1a6 6 0 0 0 2.5 2.5L12 10l3 1v2a1.5 1.5 0 0 1-1.5 1.5A8.5 8.5 0 0 1 5.5 6.5 1.5 1.5 0 0 1 7 5z" fill="#fff"/></svg>
        0412 385 976
      </li>
      <li>
        <svg class="contact-icon" viewBox="0 0 20 20" aria-hidden="true"><circle cx="10" cy="10" r="10" fill="#f28a12"/><rect x="5" y="6.5" width="10" height="7" fill="#fff"/><path d="M5 6.5l5 4 5-4" fill="none" stroke="#f28a12" stroke-width="1.2"/></svg>
        cobaltmeadow.au@postvale.net
      </li>
      <li>
        <svg class="contact-icon" viewBox="0 0 20 20" aria-hidden="true"><circle cx="10" cy="10" r="10" fill="#f28a12"/><circle cx="10" cy="10" r="5.5" fill="none" stroke="#fff" stroke-width="1.3"/><path d="M4.5 10h11M10 4.5c-2.5 3-2.5 8 0 11M10 4.5c2.5 3 2.5 8 0 11" fill="none" stroke="#fff" stroke-width="1.1"/></svg>
        www.cobalt-meadow.com.au
      </li>
    </ul>
    <div class="offer-band">Contact us now for your free 20min assessment</div>
  </section>

</body>
</html>
```